Harborline Renewal Business Card Design

Professional and clean design. The design colors should flow with the logo. Two-sided card with the website on the back which is:

www.HarborlineRenewal.example.

"Specializing in Water Damage Restoration"

On the front I need the name, email, phone, and logo.

Name: Darnell Quisby
Email: Darnell@HarborlineRenewal.example
Phone: 555-318-2046 for now

I only have the Preview and Thumbnail right now but should have the source files uploaded within a day or two.

Target Market(s)

Flood victims, home owners with water damage from busted pipes etc...

Industry/Entity Type

Business

Contact Information for Business Card

Name: Darnell Quisby

Font styles to use
Serif
Sans Serif

Requirements
Must have
• Business Card Details Info

```html
<!DOCTYPE html>
<html lang="en">
<head>
<meta charset="utf-8">
<title>Harborline Renewal Business Card</title>
<link rel="stylesheet" href="https://fonts.googleapis.com/css2?family=Cinzel:wght@600&family=Open+Sans:wght@400;600&display=swap">
<style>
  :root {
    --backdrop: #3a3431;
    --card: #0c0c0d;
    --brand-blue: #3fb3e8;
    --text-light: #f2f2f2;
  }
  * { box-sizing: border-box; margin: 0; padding: 0; }
  html, body { width: 1200px; height: 844px; overflow: hidden; }
  body {
    background: var(--backdrop);
    font-family: "Open Sans", Arial, sans-serif;
    position: relative;
  }
  .card {
    position: absolute;
    top: 279px;
    width: 500px;
    height: 286px;
    background: var(--card);
    border-radius: 3px;
    overflow: hidden;
  }
  .card--front { left: 70px; }
  .card--back { left: 630px; }

  .wordmark {
    position: absolute;
    font-family: "Cinzel", Georgia, serif;
    font-weight: 600;
    color: var(--brand-blue);
    letter-spacing: 2px;
    line-height: 1.05;
  }
  .brand-dot {
    position: absolute;
    border-radius: 50%;
    background: var(--brand-blue);
  }
  .rule {
    position: absolute;
    height: 2px;
    background: var(--brand-blue);
  }

  /* Front */
  .card--front .brand-dot { left: 78px; top: 44px; width: 52px; height: 52px; }
  .card--front .wordmark { left: 34px; top: 110px; font-size: 29px; }
  .card--front .rule--top { left: 200px; right: 170px; top: 87px; height: 1.5px; }
  .card--front .rule--bottom { left: 20px; right: 20px; top: 250px; }
  .contact {
    position: absolute;
    right: 26px;
    top: 72px;
    text-align: right;
  }
  .contact__name {
    font-weight: 600;
    font-size: 17px;
    color: var(--brand-blue);
    margin-bottom: 16px;
  }
  .contact__line {
    display: flex;
    justify-content: flex-end;
    align-items: center;
    gap: 7px;
    font-size: 12.5px;
    color: var(--text-light);
    margin-bottom: 14px;
  }
  .contact__line svg { width: 11px; height: 11px; fill: var(--brand-blue); }

  /* Back */
  .card--back .wordmark {
    left: 0; right: 0; top: 50px;
    text-align: center;
    font-size: 34px;
  }
  .website {
    position: absolute;
    left: 0; right: 0; top: 150px;
    text-align: center;
    font-size: 12.5px;
    font-weight: 600;
    color: var(--text-light);
  }
  .tagline-row {
    position: absolute;
    left: 20px; right: 20px; top: 205px;
    display: flex;
    align-items: center;
    gap: 10px;
  }
  .tagline-row .rule { position: static; flex: 1; height: 1.5px; }
  .tagline {
    font-size: 13.5px;
    font-weight: 600;
    color: var(--brand-blue);
    white-space: nowrap;
  }
</style>
</head>
<body>
  <section class="card card--front" aria-label="Business card front">
    <span class="brand-dot" aria-hidden="true"></span>
    <div class="wordmark">HARBORLINE<br>RENEWAL</div>
    <span class="rule rule--top"></span>
    <div class="contact">
      <p class="contact__name">Darnell Quisby</p>
      <p class="contact__line">555-318-2046
        <svg viewBox="0 0 24 24" aria-hidden="true"><path d="M6.6 10.8a15.1 15.1 0 0 0 6.6 6.6l2.2-2.2c.3-.3.7-.4 1-.2 1.1.4 2.3.6 3.6.6.6 0 1 .4 1 1V20c0 .6-.4 1-1 1A17 17 0 0 1 3 4c0-.6.4-1 1-1h3.5c.6 0 1 .4 1 1 0 1.3.2 2.5.6 3.6.1.3 0 .7-.2 1l-2.3 2.2z"/></svg>
      </p>
      <p class="contact__line">Darnell@HarborlineRenewal.example
        <svg viewBox="0 0 24 24" aria-hidden="true"><path d="M2 5h20v14H2z M3 6l9 7 9-7" fill="var(--brand-blue)"/></svg>
      </p>
    </div>
    <span class="rule rule--bottom"></span>
  </section>

  <section class="card card--back" aria-label="Business card back">
    <div class="wordmark">HARBORLINE RENEWAL</div>
    <p class="website">www.HarborlineRenewal.example</p>
    <div class="tagline-row">
      <span class="rule"></span>
      <p class="tagline">Specializing in Water Damage Restoration</p>
      <span class="rule"></span>
    </div>
  </section>
</body>
</html>
```